Broschüren-Design für Pizzalieferdienst
Zielgruppe
Wir sind ein Pizzalieferdienst in Südtirol.
Aufgabenstellung
Es soll eine Broschüre werden, die als Speisekarte dient und wie man sie nicht oft sieht. Ausgefallene Ideen werden bevorzugt.
Um die maximale Kreativität zu fördern wird lediglich das Logo und die Schriftart vorgegeben.
Viel Spass an alle Teilnehmer!

```html
<!DOCTYPE html>
<html lang="de">
<head>
<meta charset="utf-8">
<title>Forno Rapido Brixen – Speisekarte</title>
<link href="https://fonts.googleapis.com/css2?family=Lobster&family=Oswald:wght@700&family=Ubuntu:wght@400&display=swap" rel="stylesheet">
<style>
:root{
  --stage-top:#e8e8e8;
  --stage:#c8c8c8;
  --slate:#272727;
  --slate-light:#313131;
  --chalk:#bdbdbd;
  --gold:#e3a72f;
  --white:#fff;
  --ink:#111;
  --muted:#b9b9b9;
  --rule:#6b5a33;
}
*{margin:0;padding:0;box-sizing:border-box}
html,body{width:1200px;height:2741px;overflow:hidden}
body{position:relative;background:var(--stage);font-family:"Ubuntu",sans-serif}
.stage-top{position:absolute;left:0;top:0;width:1200px;height:862px;background:var(--stage-top)}
.sheet{position:absolute;background:radial-gradient(ellipse at 40% 35%,var(--slate-light),var(--slate) 70%);overflow:hidden}

/* cover */
.cover{width:550px;height:550px}
.cover .ingredient-ring{position:absolute;left:58px;top:27px;width:436px;height:436px}
.cover .badge{position:absolute;left:166px;top:135px;width:220px;height:220px;border-radius:50%;
  border:2px solid #4a4a4a;background:var(--slate);display:flex;align-items:center;justify-content:center}
.cover .brand{font-family:"Lobster",sans-serif;color:var(--white);font-size:32px;text-align:center;line-height:1.1}
.cover .tagline{position:absolute;left:0;width:100%;top:470px;text-align:center;font-family:"Lobster",sans-serif;color:var(--gold);font-size:21px}
.cover .rule{position:absolute;left:180px;width:190px;top:504px;height:1px;background:#5a5a5a}
.cover .delivery{position:absolute;left:0;width:100%;top:510px;text-align:center;color:var(--white);font-size:16px}

/* spreads */
.panel{position:absolute;top:0;height:550px}
.hero-photo{position:absolute;inset:0;background:linear-gradient(180deg,#1c1c1c 0%,#2a2623 40%,#7a3a22 62%,#b5502c 75%,#3a2a20 100%)}
.hero-title{position:absolute;left:66px;top:62px;font-family:"Oswald",sans-serif;font-size:72px;line-height:1;color:var(--white);letter-spacing:1px}
.hero-copy{position:absolute;left:68px;top:155px;width:336px;color:var(--white);font-size:11.5px;line-height:1.25}

.category{position:absolute;left:0;width:100%;height:106px;background:var(--white)}
.category .photo{position:absolute;left:0;top:0;width:360px;height:100%;background:linear-gradient(90deg,#6b4a2e,#d9a35a 55%,#f2e4c8 85%,var(--white))}
.category .line{position:absolute;right:140px;top:50%;width:90px;height:3px;border-top:1px solid #888;border-bottom:1px solid #888}
.category .label{position:absolute;right:38px;top:50%;transform:translateY(-42%);font-family:"Lobster",sans-serif;font-size:24px;color:var(--ink)}

.menu-row{position:absolute;display:flex;gap:22px}
.dish{width:130px;height:125px;position:relative}
.dish .name{display:flex;align-items:center;gap:4px;font-family:"Lobster",sans-serif;font-size:10.5px;color:var(--gold);white-space:nowrap}
.dish .name::after{content:"";flex:1;height:1px;background:var(--rule)}
.dish .desc{font-size:6px;color:var(--muted);line-height:1.3;margin-top:2px;height:16px}
.dish .pizza{position:absolute;left:27px;top:38px;width:76px;height:50px;border-radius:50%;
  background:radial-gradient(ellipse,#e04a2c 0%,#d8542e 55%,#f0c07a 72%,#c98a44 100%)}
.dish .price{position:absolute;left:33px;top:99px;width:62px;height:17px;background:var(--white);
  font-family:"Lobster",sans-serif;font-size:12px;color:var(--ink);text-align:center;line-height:17px}
.veggies{position:absolute;right:0;bottom:0;width:300px;height:140px;background:radial-gradient(ellipse at 70% 80%,#7ca34a,#b8a46a 40%,transparent 72%)}
</style>
</head>
<body>

<div class="stage-top"></div>

<!-- closed brochure, flat -->
<section class="sheet cover" style="left:325px;top:156px">
  <svg class="ingredient-ring" viewBox="0 0 436 436" role="img" aria-label="Kreidezeichnung von Pizzastücken und Gemüse, im Kreis um das Logo angeordnet">
    <defs>
      <radialGradient id="chalkA" cx="50%" cy="50%" r="50%">
        <stop offset="50%" stop-color="#bdbdbd" stop-opacity=".05"/>
        <stop offset="75%" stop-color="#bdbdbd" stop-opacity=".2"/>
        <stop offset="100%" stop-color="#bdbdbd" stop-opacity=".04"/>
      </radialGradient>
    </defs>
    <path d="M218 0a218 218 0 1 0 0.1 0zM218 108a110 110 0 1 1-0.1 0z" fill="url(#chalkA)" fill-rule="evenodd"/>
  </svg>
  <div class="badge"><p class="brand">Forno Rapido<br>Brixen</p></div>
  <p class="tagline">Scharf auf pizza? dann bist du hier richtig!</p>
  <div class="rule"></div>
  <p class="delivery">Aktuelle Lieferzeit: ca. 45 min</p>
</section>

<!-- cover -->
<section class="sheet cover" style="left:325px;top:912px">
  <svg class="ingredient-ring" viewBox="0 0 436 436" role="img" aria-label="Kreidezeichnung von Pizzastücken und Gemüse, im Kreis um das Logo angeordnet">
    <defs>
      <radialGradient id="chalkB" cx="50%" cy="50%" r="50%">
        <stop offset="50%" stop-color="#bdbdbd" stop-opacity=".05"/>
        <stop offset="75%" stop-color="#bdbdbd" stop-opacity=".2"/>
        <stop offset="100%" stop-color="#bdbdbd" stop-opacity=".04"/>
      </radialGradient>
    </defs>
    <path d="M218 0a218 218 0 1 0 0.1 0zM218 108a110 110 0 1 1-0.1 0z" fill="url(#chalkB)" fill-rule="evenodd"/>
  </svg>
  <div class="badge"><p class="brand">Forno Rapido<br>Brixen</p></div>
  <p class="tagline">Scharf auf pizza? dann bist du hier richtig!</p>
  <div class="rule"></div>
  <p class="delivery">Aktuelle Lieferzeit: ca. 45 min</p>
</section>

<!-- spread 1 -->
<section class="sheet" style="left:50px;top:1518px;width:1098px;height:550px">
  <div class="panel" style="left:0;width:516px">
    <div class="hero-photo" role="img" aria-label="Foto einer Pizza mit Salami, Oliven und Paprika"></div>
    <h1 class="hero-title">PIZZA</h1>
    <p class="hero-copy">Lorem ipsum tecti cum et Mopsuestia certe amni nobilis amni et quem eius hanc punico ex abstractum quem hanc vellere et et memoratur plerumque Cydno vellere domicilium nomine condidisse Mopsi condidisse tecti.</p>
  </div>
  <div class="panel" style="left:548px;width:550px">
    <div class="category" style="top:0">
      <div class="photo" role="img" aria-label="Foto einer Pizza mit zerlaufendem Käse"></div>
      <div class="line"></div><p class="label">Klassisch</p>
    </div>
    <div class="menu-row" style="left:58px;top:137px">
      <div class="dish"><p class="name">Margherita</p><p class="desc">Tomatensauce, Mozzarella, Origano</p><div class="pizza" role="img" aria-label="Foto Pizza"></div><p class="price">6.5 €</p></div>
      <div class="dish"><p class="name">Scharfe Salami</p><p class="desc">Tomatensauce, Mozzarella, scharfe Salami, Origano</p><div class="pizza" role="img" aria-label="Foto Pizza"></div><p class="price">6.5 €</p></div>
      <div class="dish"><p class="name">Thunfisch-Zwiebel</p><p class="desc">Tomatensauce, Mozzarella, Thunfisch, Zwiebel, Origano</p><div class="pizza" role="img" aria-label="Foto Pizza"></div><p class="price">6.5 €</p></div>
    </div>
    <div class="menu-row" style="left:58px;top:272px">
      <div class="dish"><p class="name">Margherita</p><p class="desc">Tomatensauce, Mozzarella, Origano</p><div class="pizza" role="img" aria-label="Foto Pizza"></div><p class="price">6.5 €</p></div>
      <div class="dish"><p class="name">Scharfe Salami</p><p class="desc">Tomatensauce, Mozzarella, scharfe Salami, Origano</p><div class="pizza" role="img" aria-label="Foto Pizza"></div><p class="price">6.5 €</p></div>
      <div class="dish"><p class="name">Thunfisch-Zwiebel</p><p class="desc">Tomatensauce, Mozzarella, Thunfisch, Zwiebel, Origano</p><div class="pizza" role="img" aria-label="Foto Pizza"></div><p class="price">6.5 €</p></div>
    </div>
    <div class="menu-row" style="left:58px;top:407px">
      <div class="dish"><p class="name">Margherita</p><p class="desc">Tomatensauce, Mozzarella, Origano</p><div class="pizza" role="img" aria-label="Foto Pizza"></div><p class="price">6.5 €</p></div>
      <div class="dish"><p class="name">Scharfe Salami</p><p class="desc">Tomatensauce, Mozzarella, scharfe Salami, Origano</p><div class="pizza" role="img" aria-label="Foto Pizza"></div><p class="price">6.5 €</p></div>
      <div class="dish"><p class="name">Thunfisch-Zwiebel</p><p class="desc">Tomatensauce, Mozzarella, Thunfisch, Zwiebel, Origano</p><div class="pizza" role="img" aria-label="Foto Pizza"></div><p class="price">6.5 €</p></div>
    </div>
  </div>
</section>

<!-- spread 2 -->
<section class="sheet" style="left:48px;top:2133px;width:1100px;height:550px">
  <div class="panel" style="left:0;width:550px">
    <div class="menu-row" style="left:60px;top:27px">
      <div class="dish"><p class="name">Margherita</p><p class="desc">Tomatensauce, Mozzarella, Origano</p><div class="pizza" role="img" aria-label="Foto Pizza"></div><p class="price">6.5 €</p></div>
      <div class="dish"><p class="name">Scharfe Salami</p><p class="desc">Tomatensauce, Mozzarella, scharfe Salami, Origano</p><div class="pizza" role="img" aria-label="Foto Pizza"></div><p class="price">6.5 €</p></div>
      <div class="dish"><p class="name">Thunfisch-Zwiebel</p><p class="desc">Tomatensauce, Mozzarella, Thunfisch, Zwiebel, Origano</p><div class="pizza" role="img" aria-label="Foto Pizza"></div><p class="price">6.5 €</p></div>
    </div>
    <div class="menu-row" style="left:60px;top:162px">
      <div class="dish"><p class="name">Margherita</p><p class="desc">Tomatensauce, Mozzarella, Origano</p><div class="pizza" role="img" aria-label="Foto Pizza"></div><p class="price">6.5 €</p></div>
      <div class="dish"><p class="name">Scharfe Salami</p><p class="desc">Tomatensauce, Mozzarella, scharfe Salami, Origano</p><div class="pizza" role="img" aria-label="Foto Pizza"></div><p class="price">6.5 €</p></div>
      <div class="dish"><p class="name">Thunfisch-Zwiebel</p><p class="desc">Tomatensauce, Mozzarella, Thunfisch, Zwiebel, Origano</p><div class="pizza" role="img" aria-label="Foto Pizza"></div><p class="price">6.5 €</p></div>
    </div>
    <div class="category" style="top:290px">
      <div class="photo" role="img" aria-label="Foto einer scharfen Pizza mit Paprika und Oliven"></div>
      <div class="line"></div><p class="label">Scharf</p>
    </div>
    <div class="menu-row" style="left:60px;top:409px">
      <div class="dish"><p class="name">Margherita</p><p class="desc">Tomatensauce, Mozzarella, Origano</p><div class="pizza" role="img" aria-label="Foto Pizza"></div><p class="price">6.5 €</p></div>
      <div class="dish"><p class="name">Scharfe Salami</p><p class="desc">Tomatensauce, Mozzarella, scharfe Salami, Origano</p><div class="pizza" role="img" aria-label="Foto Pizza"></div><p class="price">6.5 €</p></div>
      <div class="dish"><p class="name">Thunfisch-Zwiebel</p><p class="desc">Tomatensauce, Mozzarella, Thunfisch, Zwiebel, Origano</p><div class="pizza" role="img" aria-label="Foto Pizza"></div><p class="price">6.5 €</p></div>
    </div>
  </div>
  <div class="panel" style="left:552px;width:548px">
    <div class="category" style="top:0">
      <div class="photo" role="img" aria-label="Foto einer vegetarischen Pizza mit Rucola und Zwiebeln"></div>
      <div class="line"></div><p class="label">Vegetarisch</p>
    </div>
    <div class="menu-row" style="left:58px;top:139px">
      <div class="dish"><p class="name">Margherita</p><p class="desc">Tomatensauce, Mozzarella, Origano</p><div class="pizza" role="img" aria-label="Foto Pizza"></div><p class="price">6.5 €</p></div>
      <div class="dish"><p class="name">Scharfe Salami</p><p class="desc">Tomatensauce, Mozzarella, scharfe Salami, Origano</p><div class="pizza" role="img" aria-label="Foto Pizza"></div><p class="price">6.5 €</p></div>
      <div class="dish"><p class="name">Thunfisch-Zwiebel</p><p class="desc">Tomatensauce, Mozzarella, Thunfisch, Zwiebel, Origano</p><div class="pizza" role="img" aria-label="Foto Pizza"></div><p class="price">6.5 €</p></div>
    </div>
    <div class="menu-row" style="left:58px;top:274px">
      <div class="dish"><p class="name">Margherita</p><p class="desc">Tomatensauce, Mozzarella, Origano</p><div class="pizza" role="img" aria-label="Foto Pizza"></div><p class="price">6.5 €</p></div>
      <div class="dish"><p class="name">Scharfe Salami</p><p class="desc">Tomatensauce, Mozzarella, scharfe Salami, Origano</p><div class="pizza" role="img" aria-label="Foto Pizza"></div><p class="price">6.5 €</p></div>
      <div class="dish"><p class="name">Thunfisch-Zwiebel</p><p class="desc">Tomatensauce, Mozzarella, Thunfisch, Zwiebel, Origano</p><div class="pizza" role="img" aria-label="Foto Pizza"></div><p class="price">6.5 €</p></div>
    </div>
    <div class="menu-row" style="left:58px;top:409px">
      <div class="dish"><p class="name">Margherita</p><p class="desc">Tomatensauce, Mozzarella, Origano</p><div class="pizza" role="img" aria-label="Foto Pizza"></div><p class="price">6.5 €</p></div>
    </div>
    <div class="veggies" role="img" aria-label="Foto von frischem Gemüse: Zwiebeln, Spargel, Paprika, Salat"></div>
  </div>
</section>

</body>
</html>
```